Website for Barlow Fabrication & Building Ltd

General Note to all.

1. Piling and gas works are separate areas of work and should not be put together.
- the marine section should really be the piling works and should have all the barges/water piles etc.
- the gas section should have the big silo looking thing

2. I would like to add in Specialist Onsite Labour and Management in the 'our services' section. The would include the Supervisors, Coded Welders, Site Fitters and Crane and Rig Crews etc.

3. I did like it how someone had use the BFB header logo as the top of the webpage with the individual tabs above and the website starting below. Please remove the VAT number and phone number from this section.

4. I also liked how one designer incorporate the orange line with spark (from the logo) as a page separator representing the welding part of the business

5. Add in a Mission Statement - To go above and beyond in to ensure our clients projects are delivered safely, ahead of schedule, in any environment for the benefit of not only our customers but also our employees and communities we work in.

6. Add in Business Objectives -BFB is on a mission to be one of the leading contractors in UK to supply All Site Labour - ranging from Site Management, fully Coded Welders, Site Fitters and Crane and Rig Crews.

7. I am happy for you to add in photos that are not ours for the thumbs nails for the our services. ie a colourful welding pics/cool tunnelling pic etc - just make sure I will not get done for copy write infringements

8. I would like a some type of 'contact us' field or 'request a consultation' section.

9. Please confirm if the webpages you create will be compatible for both desktop and mobile app and how difficult it will be to update personally once it is live.

10. You have all done very well and have thus far been very impressed with what you have produced. I gave a very vague brief as I was not entirely sure how you would go about making something with very little information. Some of the designs look very professional.

11. I'm not sure how once I choose the winning design how that then transfers over to my domain? Perhaps someone can help me with that? I will also be looking for a web hosting platform so feel free to provide this information.

After using Sketch hive for successful getting a professional logo for the company I'm giving the web design option a go.

I am looking for a professional website for the above civil construction company.

The company director has many years experience in Marine, tunnelling, conveyors, stadium construction gas and piling works including piling works for coal ports, bridges and tunnels.

The company currently provide 20+ skilled and experienced guys from all trades (supervisors, coded welders, fitters, crane drivers and crane supervisors, rigglers, slingers and piling operatives) on the Corran Shoreline project in London - London's new super sewer. Most of this work is off barges carrying cranes (upto 600T and drill rigs).

As we are looking to expand and get more subcontracts we need a web presence to say who we are and what we do.

I'll include the 2 company logos we currently use below

I have included an info doc with pics you may or may not use.

Target Market(s)

Mainly other large construction companies and potential subcontractors

Industry/Entity Type

Construction Company

Coding

Coded - Design and coding required

Font styles to use
Sans Serif

Colors
0655a3
f37122
ffffff

Requirements
Must have
• Few tabs
• Simple to use/update but still professional look
• The challenge will be making the website look professional with not much available content.
Should not have
• No residential house building

```html
<!DOCTYPE html>
<html lang="en">
<head>
<meta charset="utf-8">
<title>Barlow Fabrication & Building Ltd</title>
<link href="https://fonts.googleapis.com/css2?family=Lato:wght@400;700;900&display=swap" rel="stylesheet">
<style>
:root{
  --blue:#0655a3;
  --navy:#0d3f73;
  --orange:#f37122;
  --white:#ffffff;
  --ink:#2b2b2b;
  --grey:#6b6b6b;
  --paper:#f4f4f4;
}
*{box-sizing:border-box;margin:0;padding:0}
html,body{width:1200px;height:4321px;overflow:hidden}
body{font-family:'Lato',sans-serif;color:var(--ink);background:var(--white);position:relative}
section,header,footer,nav{position:absolute;left:0;width:1200px}
.photo{position:absolute}
h2.section-title{position:absolute;left:0;width:1200px;text-align:center;font-size:17px;font-weight:700;letter-spacing:1px;text-transform:uppercase}

/* top bar */
.top-bar{top:0;height:30px;background:var(--navy);color:var(--white);font-size:11px}
.top-bar .reg{position:absolute;left:132px;top:9px}
.top-bar .contact{position:absolute;left:640px;top:9px}
.top-bar .cta{position:absolute;left:970px;top:0;width:180px;height:30px;background:var(--orange);font-size:9px;font-weight:700;display:flex;align-items:center;justify-content:center;text-transform:uppercase}
/* nav */
.main-nav{top:30px;height:110px;background:var(--white)}
.main-nav ul{list-style:none;position:absolute;top:63px;display:flex;gap:36px;font-size:12px;font-weight:700;color:var(--navy)}
.main-nav .left{left:156px}
.main-nav .right{left:702px}
.main-nav .active{color:var(--orange);border:1px solid var(--orange);border-radius:12px;padding:3px 10px;margin:-4px -10px}
.logo{position:absolute;left:498px;top:8px;width:204px;height:100px;display:flex;align-items:center;justify-content:center;gap:8px}
.logo .mark{width:22px;height:22px;border-radius:50%;background:var(--orange)}
.logo span{font-weight:900;font-size:34px;color:var(--navy)}

/* hero */
.hero{top:140px;height:480px}
.hero .photo{left:0;top:0;width:1200px;height:480px;background:linear-gradient(180deg,#8fb2d6 0%,#c9a67f 45%,#5a4a3a 72%,#2d3846 100%)}
.hero h1{position:absolute;left:143px;top:140px;font-size:30px;font-weight:900;color:var(--navy)}
.hero h1 em{font-style:normal;color:var(--orange)}
.hero p{position:absolute;left:143px;top:180px;width:340px;font-size:11px;color:var(--white);line-height:1.5}
.btn{background:var(--orange);color:var(--white);font-size:10px;font-weight:700;text-transform:uppercase;border-radius:14px;display:flex;align-items:center;justify-content:center}
.hero .btn{position:absolute;left:143px;top:244px;width:120px;height:30px}
.arrow-btn{position:absolute;width:26px;height:26px;background:rgba(255,255,255,.8);display:flex;align-items:center;justify-content:center;color:var(--grey);font-size:14px}
.hero .prev{left:88px;top:180px}.hero .next{left:1078px;top:180px}
.wave{position:absolute;left:0}

/* about */
.about{top:590px;height:380px}
.about .photo{left:132px;top:50px;width:368px;height:286px;background:linear-gradient(180deg,#aac3de,#7d8a8c 55%,#4a5a52)}
.about .frame{position:absolute;left:122px;top:40px;width:100px;height:100px;border-left:4px solid var(--orange);border-top:4px solid var(--orange)}
.about h2{position:absolute;left:548px;top:58px;font-size:20px;font-weight:700;color:var(--navy)}
.about .text{position:absolute;left:548px;top:92px;width:530px;font-size:10.5px;line-height:1.6;color:var(--grey)}
.about .text h3{font-size:11px;font-weight:700;color:var(--orange);text-transform:uppercase;margin-top:7px}
.about a{position:absolute;left:548px;top:338px;font-size:11px;font-weight:700;color:var(--navy);text-decoration:underline}

/* sectors */
.sectors{top:955px;height:405px}
.sectors .photo{left:0;top:0;width:1200px;height:405px;background:linear-gradient(180deg,#1d5e9e,#2a5f8e 60%,#123b66)}
.sectors h2.section-title{top:92px;color:var(--white)}
.sector-list{position:absolute;left:160px;top:185px;width:880px;display:flex;justify-content:space-between;list-style:none}
.sector-list li{width:120px;text-align:center;color:var(--white);font-size:9px;font-weight:700;text-transform:uppercase;line-height:1.4}
.sector-list .icon{width:68px;height:68px;border:2px solid var(--white);border-radius:50%;margin:0 auto 12px;display:flex;align-items:center;justify-content:center;background:rgba(255,255,255,.08)}
.sectors .labour-note{position:absolute;left:250px;top:330px;width:700px;text-align:center;color:var(--white);font-size:11px;line-height:1.6}
.sectors .labour-note b{color:var(--orange)}

/* team */
.team{top:1360px;height:360px;background:var(--white)}
.team h2.section-title{top:62px;color:var(--ink)}
.member{position:absolute;top:120px;width:195px}
.member .photo{position:static;width:195px;height:130px}
.member h3{font-size:11px;font-weight:700;margin-top:8px}
.member p{font-size:9px;color:var(--grey);margin-top:3px}

/* projects */
.projects{top:1720px;height:648px}
.projects .bg{position:absolute;inset:0;background:linear-gradient(180deg,#0b4a8c,#0c3e72)}
.projects h2.section-title{top:50px;color:var(--white)}
.filters{position:absolute;left:0;width:1200px;top:110px;display:flex;justify-content:center;gap:26px;list-style:none;font-size:10px;color:var(--white)}
.filters .on{background:var(--orange);padding:3px 8px;margin:-3px -8px}
.tile{position:absolute;width:292px;height:186px}
.tile.feature{background:var(--white);text-align:center}
.tile.feature h3{font-size:15px;color:var(--ink);margin-top:46px;font-weight:700}
.tile.feature p{font-size:9px;color:var(--grey);margin:10px 42px 0;line-height:1.5}
.tile.feature .btn{width:104px;height:26px;margin:12px auto 0;border-radius:3px}
.tile.feature .frame{position:absolute;inset:10px;border:1px solid #ddd}

/* testimonials */
.testimonials{top:2368px;height:397px}
.testimonials .bg{position:absolute;inset:0;background:linear-gradient(180deg,#f37122,#e0631a)}
.testimonials h2.section-title{top:62px;color:var(--white)}
.quote{position:absolute;top:147px;width:244px;height:161px;border:1px solid rgba(255,255,255,.6);border-radius:12px;text-align:center;color:var(--white)}
.quote .avatar{width:56px;height:56px;border-radius:50%;border:3px solid var(--white);background:#d7a27a;margin:-28px auto 0}
.quote p{font-size:10px;line-height:1.5;margin:14px 22px 0}
.quote h3{font-size:10px;font-weight:700;margin-top:12px}
.testimonials .prev{left:140px;top:232px;background:rgba(255,255,255,.3);border-radius:50%;color:var(--white)}
.testimonials .next{left:1034px;top:232px;background:rgba(255,255,255,.3);border-radius:50%;color:var(--white)}

/* contact */
.contact{top:2765px;height:485px}
.contact .bg{position:absolute;inset:0;background:linear-gradient(180deg,#2a3037,#1b1f24)}
.contact h2.section-title{top:58px;color:var(--white)}
.field{position:absolute;background:#e9e9e9;font-size:10px;color:#999;padding:0 12px;display:flex;align-items:center;height:44px}
.field.msg{align-items:flex-start;padding-top:12px;height:97px}
.contact .btn{position:absolute;left:531px;top:397px;width:148px;height:38px;border-radius:19px}

/* blog */
.blog{top:3250px;height:330px;background:var(--paper)}
.blog h2.section-title{top:62px;color:var(--ink)}
.post{position:absolute;top:137px;height:164px}
.post .photo{left:0;top:0;width:190px;height:164px}
.post .card{position:absolute;left:140px;top:20px;width:270px;height:126px;background:var(--white);box-shadow:0 2px 8px rgba(0,0,0,.12);padding:14px 16px;font-size:10px}
.post .card h3{font-size:11px;font-weight:700}
.post .card time{display:block;font-size:8px;color:var(--grey);margin-top:3px}
.post .card p{color:var(--grey);line-height:1.5;margin-top:6px}
.post .card a{color:var(--navy);font-weight:700;text-decoration:underline}

/* clients */
.clients{top:3573px;height:368px}
.clients .skyline{position:absolute;left:0;top:0;width:1200px;height:90px;background:linear-gradient(180deg,rgba(6,85,163,0) 0%,rgba(6,85,163,.55) 40%,var(--navy) 100%)}
.clients .bg{position:absolute;left:0;top:88px;width:1200px;height:280px;background:var(--navy)}
.clients h2.section-title{top:148px;color:var(--white)}
.client-logos{position:absolute;left:132px;top:206px;display:flex;gap:32px;list-style:none}
.client-logos li{width:136px;height:74px;background:var(--white);display:flex;align-items:center;justify-content:center;gap:6px;font-size:15px;font-weight:700;color:var(--navy)}
.client-logos .dot{width:10px;height:10px;background:var(--orange)}

/* footer */
.site-footer{top:3941px;height:380px;background:linear-gradient(180deg,#20262c,#14181c);color:#cfd3d6}
.col{position:absolute;top:62px;font-size:10px;line-height:1.9}
.col h4{font-size:10px;font-weight:700;color:var(--white);text-transform:uppercase;margin-bottom:8px}
.col ul{list-style:none}
.col .row{display:flex;gap:10px;align-items:flex-start;margin-bottom:14px}
.socials{display:flex;gap:10px}
.socials span{width:18px;height:18px;border-radius:50%;background:var(--blue);display:block}
.socials span:nth-child(3){background:var(--orange)}
.copyright{position:absolute;left:140px;top:352px;font-size:8px;color:#8a9096}
</style>
</head>
<body>

<header class="top-bar">
  <div class="reg">Company Register No : 4471203</div>
  <div class="contact">✉ E-Mail us : info@bfb-build.example</div>
  <div class="cta">Request a Consultation</div>
</header>

<nav class="main-nav">
  <ul class="left"><li class="active">Home</li><li>About us</li><li>What we do</li><li>Services</li></ul>
  <div class="logo"><div class="mark"></div><span>BFB</span></div>
  <ul class="right"><li>Our Projects</li><li>Our Team</li><li>Blog</li><li>Contact us</li></ul>
</nav>

<section class="hero">
  <div class="photo" role="img" aria-label="Piling barge with crane working on a river at dusk"></div>
  <h1>BUILDING <em>BETTER, FASTER</em></h1>
  <p>Lorem ipsum dolor sit amet, consectetur adipiscing elit. Aenean commodo ligula eget dolor. Aenean massa cum sociis natoque.</p>
  <div class="btn">Read More</div>
  <div class="arrow-btn prev">‹</div><div class="arrow-btn next">›</div>
  <svg class="wave" style="top:405px" width="1200" height="80" viewBox="0 0 1200 80" preserveAspectRatio="none">
    <path d="M0 42 C300 78 820 70 1200 14 L1200 80 L0 80Z" fill="var(--orange)"/>
    <path d="M0 52 C300 86 820 78 1200 24 L1200 80 L0 80Z" fill="var(--white)"/>
  </svg>
</section>

<section class="about">
  <div class="frame"></div>
  <div class="photo" role="img" aria-label="Orange piling rig on a barge beside a crane"></div>
  <h2>BARLOW FABRICATION &amp; BUILDING</h2>
  <div class="text">
    <p>Barlow Fabrication &amp; Building has over 15 years experience in civil construction, currently supplying skilled crews to the Corran Shoreline project in London. Notable projects include Eastmere Bridge, the coal berths at Port Calder and the Wynd River Bridge in the Northern Territory.</p>
    <h3>Mission Statement</h3>
    <p>To go above and beyond to ensure our clients' projects are delivered safely, ahead of schedule, in any environment, for the benefit of not only our customers but also our employees and the communities we work in.</p>
    <h3>Business Objectives</h3>
    <p>BFB is on a mission to be one of the leading contractors in the UK to supply all site labour, ranging from Site Management, fully Coded Welders and Site Fitters to Crane and Rig Crews.</p>
  </div>
  <a>Read More</a>
</section>

<section class="sectors">
  <div class="photo" role="img" aria-label="Blue tinted photo of a construction site"></div>
  <svg class="wave" style="top:-2px" width="1200" height="70" viewBox="0 0 1200 70" preserveAspectRatio="none">
    <path d="M0 0 L1200 0 L1200 6 C880 62 320 66 0 14Z" fill="var(--white)"/>
    <path d="M720 44 C900 36 1060 22 1200 6 L1200 14 C1060 32 900 44 720 44Z" fill="var(--orange)"/>
  </svg>
  <h2 class="section-title">Sectors that we operate</h2>
  <ul class="sector-list">
    <li><div class="icon"><svg width="34" height="30" viewBox="0 0 34 30" fill="none" stroke="#fff" stroke-width="2"><path d="M2 22h30l-4 6H6z"/><path d="M10 22V8h6v14M22 22V2"/></svg></div>Marine</li>
    <li><div class="icon"><svg width="34" height="30" viewBox="0 0 34 30" fill="none" stroke="#fff" stroke-width="2"><path d="M4 28h26M8 28V6h6v22M20 28V12h8v16M8 6l6 6"/></svg></div>Piling</li>
    <li><div class="icon"><svg width="34" height="30" viewBox="0 0 34 30" fill="none" stroke="#fff" stroke-width="2"><path d="M9 12a8 8 0 0 1 16 0H7zM8 28c0-6 4-10 9-10s9 4 9 10"/></svg></div>Specialist Onsite<br>Labour</li>
    <li><div class="icon"><svg width="34" height="30" viewBox="0 0 34 30" fill="none" stroke="#fff" stroke-width="2"><rect x="8" y="3" width="14" height="25" rx="2"/><path d="M11 8h8v6h-8zM22 10h4v12"/></svg></div>Gas<br>Works</li>
    <li><div class="icon"><svg width="34" height="30" viewBox="0 0 34 30" fill="none" stroke="#fff" stroke-width="2"><path d="M3 28V16a14 14 0 0 1 28 0v12M10 28V18a7 7 0 0 1 14 0v10"/></svg></div>Tunnelling</li>
    <li><div class="icon"><svg width="34" height="30" viewBox="0 0 34 30" fill="none" stroke="#fff" stroke-width="2"><path d="M2 18h30M6 18v10M28 18v10M6 6v12M28 6v12M6 8c6 8 16 8 22 0"/></svg></div>Bridge &amp; Stadium<br>Construction</li>
  </ul>
  <p class="labour-note"><b>Specialist Onsite Labour &amp; Management</b> — Supervisors, Coded Welders, Site Fitters and Crane and Rig Crews.</p>
</section>

<section class="team">
  <h2 class="section-title">Our Team</h2>
  <div class="member" style="left:132px"><div class="photo" role="img" aria-label="Company director in a suit at a building site" style="background:linear-gradient(180deg,#cfd9e4,#6f7884)"></div><h3>Owen R. Hale</h3><p>Company Director</p></div>
  <div class="member" style="left:368px"><div class="photo" role="img" aria-label="Construction manager in a red hard hat" style="background:linear-gradient(180deg,#9ec3e2,#c94a3a)"></div><h3>Rory Tamblin</h3><p>Construction Manager</p></div>
  <div class="member" style="left:624px"><div class="photo" role="img" aria-label="Construction manager in high visibility vest on site" style="background:linear-gradient(180deg,#b7b5ad,#d98a3a)"></div><h3>Neil Pascoe</h3><p>Construction Manager</p></div>
  <div class="member" style="left:872px"><div class="photo" role="img" aria-label="Rigger working at height against the sky" style="background:linear-gradient(180deg,#4f8bc4,#c9d6e2)"></div><h3>Dale Fenwick</h3><p>Rigger</p></div>
</section>

<section class="projects">
  <div class="bg" role="img" aria-label="Dark blue tinted photo of cranes on a waterfront"></div>
  <h2 class="section-title">Our Projects</h2>
  <ul class="filters"><li class="on">All</li><li>Marine</li><li>Piling</li><li>Tunnelling</li><li>Gas works</li><li>Specialist Onsite Labour</li><li>Bridge Construction</li><li>Stadium Construction</li></ul>
  <div class="tile feature" style="left:132px;top:177px"><div class="frame"></div><h3>London's new 'super sewer'</h3><p>Lorem ipsum dolor sit amet, consectetuer adipiscing elit. Aenean commodo ligula eget dolor.</p><div class="btn">Read More</div></div>
  <div class="tile" role="img" aria-label="Piling barge moored on a river" style="left:456px;top:177px;background:linear-gradient(180deg,#8fa9c4,#4d5c5a 60%,#6f7d86)"></div>
  <div class="tile" role="img" aria-label="Steel shaft with ladders inside a cofferdam" style="left:776px;top:177px;background:linear-gradient(180deg,#6c7884,#3a4048)"></div>
  <div class="tile" role="img" aria-label="Sheet pile wall at river level" style="left:132px;top:406px;background:linear-gradient(180deg,#9bb9d6,#8a5a32 55%,#c89b2a)"></div>
  <div class="tile" role="img" aria-label="Red steel rig structure under a blue sky" style="left:456px;top:406px;background:linear-gradient(180deg,#6ea2d4,#8d4a3a 70%,#5b4a40)"></div>
  <div class="tile" role="img" aria-label="Cranes over a river at sunset" style="left:776px;top:406px;background:linear-gradient(180deg,#5a6a80,#d29a64 65%,#3a3a40)"></div>
</section>

<section class="testimonials">
  <div class="bg" role="img" aria-label="Orange tinted photo of a construction yard"></div>
  <svg class="wave" style="top:-2px" width="1200" height="50" viewBox="0 0 1200 50" preserveAspectRatio="none"><path d="M0 0H1200V18C800 40 400 44 0 14Z" fill="var(--navy)"/></svg>
  <h2 class="section-title">Client Testimonials</h2>
  <div class="arrow-btn prev">‹</div><div class="arrow-btn next">›</div>
  <div class="quote" style="left:185px"><div class="avatar" role="img" aria-label="Client portrait"></div><p>Lorem ipsum dolor sit amet, consectetuer adipiscing elit. Aenean commodo ligula eget dolor. Aenean massa.</p><h3>Harlan Moorcroft</h3></div>
  <div class="quote" style="left:470px"><div class="avatar" role="img" aria-label="Client portrait" style="background:#7fa88a"></div><p>Lorem ipsum dolor sit amet, consectetuer adipiscing elit. Aenean commodo ligula eget dolor. Aenean massa.</p><h3>Tobin</h3></div>
  <div class="quote" style="left:756px"><div class="avatar" role="img" aria-label="Client portrait" style="background:#b89a86"></div><p>Lorem ipsum dolor sit amet, consectetuer adipiscing elit. Aenean commodo ligula eget dolor. Aenean massa.</p><h3>Marisol</h3></div>
  <svg class="wave" style="top:350px" width="1200" height="48" viewBox="0 0 1200 48" preserveAspectRatio="none">
    <path d="M0 8C400 44 800 44 1200 16V48H0Z" fill="var(--blue)"/>
    <path d="M0 18C400 50 800 50 1200 26V48H0Z" fill="#2a3037"/>
  </svg>
</section>

<section class="contact">
  <div class="bg" role="img" aria-label="Dark photo of workers on a site at night"></div>
  <h2 class="section-title">Contact us</h2>
  <div class="field" style="left:238px;top:132px;width:342px">Name</div>
  <div class="field" style="left:615px;top:132px;width:342px">Phone Number</div>
  <div class="field" style="left:238px;top:200px;width:719px">E-mail Address</div>
  <div class="field msg" style="left:238px;top:270px;width:719px">Message</div>
  <div class="btn">Submit</div>
</section>

<section class="blog">
  <h2 class="section-title">Latest Blog</h2>
  <div class="post" style="left:158px"><div class="photo" role="img" aria-label="Piling rig beside a steel frame on site" style="background:linear-gradient(180deg,#6fa1d0,#a0702e 60%,#5a4a3a)"></div>
    <div class="card"><h3>Lorem ipsum dolor sit amet,</h3><time>09.07.2018</time><p>Lorem ipsum dolor sit amet, consectetuer adipiscing elit. Aenean commodo ligula eget dolor.</p><a>Read More</a></div></div>
  <div class="post" style="left:645px"><div class="photo" role="img" aria-label="Dark steel shaft structure under cloudy sky" style="background:linear-gradient(180deg,#8fa2b6,#2f3338)"></div>
    <div class="card"><h3>Lorem ipsum dolor sit amet,</h3><time>09.07.2018</time><p>Lorem ipsum dolor sit amet, consectetuer adipiscing elit. Aenean commodo ligula eget dolor.</p><a>Read More</a></div></div>
</section>

<section class="clients">
  <div class="skyline" role="img" aria-label="Silhouette of cranes and city buildings"></div>
  <div class="bg"></div>
  <h2 class="section-title">Meet our Clients</h2>
  <ul class="client-logos">
    <li><span class="dot"></span>Corran</li><li>Keld</li><li>Ardent</li><li>Stonebay</li><li>Rennick</li><li>Halvor</li>
  </ul>
</section>

<footer class="site-footer">
  <div class="col" style="left:150px"><h4>Quick Links</h4><ul><li>Home</li><li>About us</li><li>What we do</li><li>Services we offer</li><li>Projects</li><li>Blog</li><li>Contact us</li></ul></div>
  <div class="col" style="left:350px"><h4>Contact us</h4>
    <div class="row"><span style="color:var(--white)">⌖</span><span>14 Quayside Row<br>Harbourton HB2 7QT</span></div>
    <div class="row"><span style="color:var(--white)">☎</span><span>07700 900418</span></div>
    <div class="row"><span style="color:var(--white)">✉</span><span>contact@bfb-build.example<br>info@bfb-build.example</span></div></div>
  <div class="col" style="left:568px"><h4>Social Links</h4><div class="socials"><span></span><span></span><span></span><span></span></div></div>
  <div class="col" style="left:810px"><h4>Sectors that we operate</h4><ul><li>Marine</li><li>Piling</li><li>Tunnelling</li><li>Gas works</li><li>Specialist Onsite Labour</li><li>Bridge Construction</li><li>Stadium Construction</li></ul></div>
  <div class="copyright">©bfb-build.example All Rights Reserved</div>
</footer>

</body>
</html>
```